Business Card Design

My business is writing crime novels to entertain readers. I write legal thrillers and mysteries. I need a card for publishers, agents, other authors, and media.

Industry/Entity Type

Legal

Contact Information for Business Card

Paul Derrow
www.derrowfiction.example
pauljderrow@inkpost.example
0064 27 5190472

```html
<!DOCTYPE html>
<html lang="en">
<head>
<meta charset="utf-8">
<title>Paul Derrow – Business Card</title>
<link rel="stylesheet" href="https://fonts.googleapis.com/css2?family=Lato:wght@400;700&family=Open+Sans:wght@400&display=swap">
<style>
  :root {
    --page-bg: #e4e4e6;
    --card-bg: #2c2c31;
    --text-light: #ffffff;
    --text-soft: #f2f2f2;
    --portrait-light: #6d6d72;
    --portrait-mid: #45454b;
    --portrait-dark: #2c2c31;
  }
  * { margin: 0; padding: 0; box-sizing: border-box; }
  html, body {
    width: 1200px;
    height: 772px;
    overflow: hidden;
    background: var(--page-bg);
  }
  .business-card {
    position: absolute;
    left: 60px;
    top: 78px;
    width: 1080px;
    height: 615px;
    border-radius: 44px;
    background: var(--card-bg);
    overflow: hidden;
  }
  .identity {
    position: absolute;
    left: 180px;
    top: 100px;
    color: var(--text-light);
  }
  .identity__name {
    font-family: 'Lato', sans-serif;
    font-size: 60px;
    line-height: 1;
    font-weight: 400;
    letter-spacing: 0.5px;
    text-transform: uppercase;
  }
  .identity__name strong { font-weight: 700; }
  .identity__role {
    margin-top: 8px;
    margin-left: 3px;
    font-family: 'Lato', sans-serif;
    font-size: 21px;
    font-weight: 400;
    letter-spacing: 0.5px;
    text-transform: uppercase;
  }
  .contact-list {
    position: absolute;
    left: 133px;
    top: 388px;
    list-style: none;
  }
  .contact-list__item {
    display: flex;
    align-items: center;
    height: 36px;
    margin-bottom: 26px;
    font-family: 'Open Sans', sans-serif;
    font-size: 24px;
    letter-spacing: 1.4px;
    color: var(--text-soft);
  }
  .contact-list__icon {
    width: 26px;
    height: 26px;
    margin-right: 21px;
    flex: none;
    fill: var(--text-soft);
  }
  .portrait {
    position: absolute;
    left: 670px;
    top: 64px;
    width: 410px;
    height: 551px;
    border-radius: 180px 180px 0 0;
    background:
      radial-gradient(ellipse 45% 30% at 50% 28%, var(--portrait-light), transparent 75%),
      linear-gradient(180deg, var(--portrait-mid) 0%, #1d1d20 70%, #151517 100%);
  }
</style>
</head>
<body>
  <div class="business-card">
    <header class="identity">
      <h1 class="identity__name"><strong>Paul</strong> Derrow</h1>
      <p class="identity__role">Owner</p>
    </header>

    <ul class="contact-list">
      <li class="contact-list__item">
        <svg class="contact-list__icon" viewBox="0 0 26 26" aria-hidden="true">
          <path d="M2 3h22v15H2z M4.5 5.5v10h17v-10z" fill-rule="evenodd"/>
          <rect x="11" y="18" width="4" height="3"/>
          <rect x="7" y="21" width="12" height="2"/>
        </svg>
        <span>www.derrowfiction.example</span>
      </li>
      <li class="contact-list__item">
        <svg class="contact-list__icon" viewBox="0 0 26 26" aria-hidden="true">
          <path d="M2 5h22v16H2z M4 7.5v11.5h18V7.5l-9 7z M5 7l8 6.2L21 7z" fill-rule="evenodd"/>
        </svg>
        <span>pauljderrow@inkpost.example</span>
      </li>
      <li class="contact-list__item">
        <svg class="contact-list__icon" viewBox="0 0 26 26" aria-hidden="true">
          <path d="M2 9c0-3 5-5 11-5s11 2 11 5v2h-5V8.5c-2-.8-4-1-6-1s-4 .2-6 1V11H2z"/>
          <path d="M8 11h10l4 6v5H4v-5z M13 14.5a2.5 2.5 0 1 0 0.01 0z" fill-rule="evenodd"/>
        </svg>
        <span>0064 27 5190472</span>
      </li>
    </ul>

    <div class="portrait" role="img" aria-label="Portrait photograph of the author in a dark leather jacket and white shirt"></div>
  </div>
</body>
</html>
```